TK Stationery - Modern Contemporary

Develop modern template for Letterhead and Stationery (business card, letterhead, envelopes) using the TK Logo and Icon

Colors
0054AA
0677BA
7BADD7
CADEEF
E8F1F8
00AB8E
00BBA5
67D7C9
C6EFE9
E9F9F6
EE7325
F08F49
F5BC92
FAE3D3
FDF4ED
6B429C
8869AF
B7A5CE
E3DAEB
F3F0F8

```html
<!DOCTYPE html>
<html lang="en">
<head>
<meta charset="utf-8">
<title>TK Stationery</title>
<link href="https://fonts.googleapis.com/css2?family=Open+Sans:wght@400;600&family=Poppins:wght@400;500;600&display=swap" rel="stylesheet">
<style>
:root{
  --backdrop:#dcdfe7;
  --paper:#ffffff;
  --navy:#2a2f4a;
  --green:#22b573;
  --orange:#f28a2e;
  --body-text:#5a5a5a;
  --pattern:#323859;
  --sign-fill:#e6e7ec;
}
*{margin:0;padding:0;box-sizing:border-box}
html,body{width:1200px;height:909px;overflow:hidden;background:var(--backdrop)}
body{position:relative;font-family:"Open Sans",sans-serif}
.sheet{position:absolute;background:var(--paper);overflow:hidden}
.wordmark{position:absolute;font-family:"Poppins",sans-serif;font-weight:500;color:var(--navy);white-space:nowrap;line-height:1;display:flex;align-items:center}
.wordmark .dot{display:inline-block;border-radius:50%;background:var(--orange);margin-left:.25em;width:.22em;height:.22em}
.wordmark.light{color:#fff}
.contact{position:absolute;font-family:"Poppins",sans-serif;color:var(--navy)}
.contact li{list-style:none;display:flex;align-items:center;white-space:nowrap}
.contact svg{flex:none}
.divider{position:absolute;width:1px;background:var(--green)}
.footer-rule{position:absolute;left:0;right:0;background:var(--green)}
.footer-band{position:absolute;left:0;right:0;bottom:0;background:var(--navy);color:#fff;font-family:"Poppins",sans-serif;display:flex;align-items:center;justify-content:center}
.pin{position:absolute;transform:translate(-50%,-50%)}

/* letterhead */
.letterhead{left:114px;top:197px;width:451px;height:581px}
.letterhead .wordmark{left:38px;top:22px;font-size:27px}
.letterhead .divider{left:285px;top:16px;height:37px}
.letterhead .contact{left:295px;top:15px;font-size:9.4px;line-height:12.4px}
.letterhead .contact li{gap:4px}
.letter-body{position:absolute;left:43px;top:113px;width:364px;font-size:7.4px;line-height:13px;color:var(--body-text)}
.letter-body p{margin-bottom:13px;text-align:justify}
.letter-body .meta{line-height:8.7px;margin-bottom:17px}
.letter-body .date{margin-bottom:9px}
.letter-body .closing{margin-top:18px;margin-bottom:6px}
.signature{display:block;width:103px;height:14px;background:var(--sign-fill);border-radius:3px;margin-bottom:5px}
.signer{font-size:8.8px;font-weight:600;color:#444;line-height:12px}
.role{font-size:7.4px;line-height:12px}
.letterhead .footer-rule{top:555px;height:3px}
.letterhead .footer-band{height:23px;font-size:9.2px}

/* business card front */
.card-front{left:623px;top:137px;width:194px;height:120px}
.card-front .wordmark{left:13px;top:53px;font-size:13px}
.card-front .divider{left:100px;top:31px;height:45px;background:#d6d8e0}
.card-front .name{position:absolute;left:108px;top:30px;font-family:"Poppins",sans-serif;font-weight:600;font-size:8.2px;color:var(--navy);line-height:9px}
.card-front .title{position:absolute;left:108px;top:39px;font-family:"Poppins",sans-serif;font-size:5.6px;color:var(--navy)}
.card-front .contact{left:108px;top:50px;font-size:5.6px;line-height:7.3px}
.card-front .contact li{gap:2px}
.card-front .footer-rule{top:103px;height:2px}
.card-front .footer-band{height:15px;font-size:5.6px}

/* business card back */
.card-back{left:833px;top:137px;width:194px;height:120px;background:var(--navy)}
.card-back .pattern{position:absolute;inset:0;background:linear-gradient(135deg,var(--pattern),var(--navy))}
.card-back .wordmark{left:100px;top:95px;font-size:10.5px}

/* envelope front */
.envelope-front{left:602px;top:311px;width:452px;height:227px}
.envelope-front .wordmark{left:31px;top:25px;font-size:25px}
.envelope-front .footer-rule{top:201px;height:3px}
.envelope-front .footer-band{height:23px;font-size:9.2px}

/* envelope back */
.envelope-back{left:602px;top:552px;width:452px;height:226px}
.envelope-back .flap{position:absolute;left:0;top:0}
.envelope-back .wordmark{left:0;right:0;top:14px;justify-content:center;font-size:24px}
</style>
</head>
<body>

<svg width="0" height="0" style="position:absolute" aria-hidden="true">
  <defs>
    <symbol id="icon-phone" viewBox="0 0 20 20">
      <circle cx="10" cy="10" r="10" fill="#f28a2e"/>
      <path d="M7 5.5l2 2.2-1 1.2c.6 1.4 1.6 2.4 3 3l1.2-1 2.2 2-1.2 1.6c-3.6-.4-6.9-3.7-7.3-7.3z" fill="#fff"/>
    </symbol>
    <symbol id="icon-mail" viewBox="0 0 20 20">
      <circle cx="10" cy="10" r="10" fill="#f28a2e"/>
      <rect x="5" y="6.5" width="10" height="7" rx="1" fill="#fff"/>
      <path d="M5.4 7l4.6 3.6L14.6 7" fill="none" stroke="#f28a2e" stroke-width="1"/>
    </symbol>
    <symbol id="icon-globe" viewBox="0 0 20 20">
      <circle cx="10" cy="10" r="10" fill="#f28a2e"/>
      <circle cx="10" cy="10" r="5" fill="none" stroke="#fff" stroke-width="1.3"/>
      <path d="M5 10h10M10 5c-2.2 2.8-2.2 7.2 0 10M10 5c2.2 2.8 2.2 7.2 0 10" fill="none" stroke="#fff" stroke-width="1"/>
    </symbol>
    <symbol id="icon-pin" viewBox="0 0 20 20">
      <circle cx="10" cy="10" r="10" fill="#f28a2e"/>
      <path d="M10 4.5a3.6 3.6 0 0 0-3.6 3.6c0 2.7 3.6 6.9 3.6 6.9s3.6-4.2 3.6-6.9A3.6 3.6 0 0 0 10 4.5z" fill="#fff"/>
      <circle cx="10" cy="8.1" r="1.4" fill="#f28a2e"/>
    </symbol>
  </defs>
</svg>

<!-- Letterhead -->
<section class="sheet letterhead">
  <div class="wordmark">teva kora<span class="dot"></span></div>
  <div class="divider"></div>
  <ul class="contact">
    <li><svg width="11" height="11"><use href="#icon-phone"/></svg>044-987 650 412</li>
    <li><svg width="11" height="11"><use href="#icon-mail"/></svg>hello@tevakora.com</li>
    <li><svg width="11" height="11"><use href="#icon-globe"/></svg>www.tevakora.com</li>
  </ul>
  <div class="letter-body">
    <p class="meta date">Issuing Date: May 5, 2018</p>
    <p class="meta">Name Of Employee Mr. XYZABC<br>Address of Employee<br>Address Line 2 etc..</p>
    <p>Dear Mr.XYZABC</p>
    <p>Lorem Ipsum has been the industry's standard dummy text ever since the 1500s, when an unknown printer took a galley of type and scrambled it to make a type specimen book. It has survived not only five centuries, but also the leap into electronic typesetting, remaining essentially unchanged. It was popularised in the 1960s with the release of Letraset sheets containing Lorem Ipsum passages, and more recently with desktop publishing software like Aldus PageMaker including versions of Lorem Ipsum.</p>
    <p>Lorem Ipsum is simply dummy text of the printing and typesetting industry. Lorem Ipsum has been the industry's standard dummy text ever since the 1500s, when an unknown printer took a galley of type and scrambled it to make a type specimen book.</p>
    <p>It has survived not only five centuries, but also the leap into electronic typesetting, remaining essentially unchanged. It was popularised in the 1960s with the release of Letraset sheets containing Lorem IpsumIpsum passages.</p>
    <p class="closing">Yours Sincerely</p>
    <span class="signature" role="img" aria-label="Handwritten signature of Daniel Morris"></span>
    <div class="signer">Daniel Morris</div>
    <div class="role">Managing Director</div>
  </div>
  <div class="footer-rule"></div>
  <svg class="pin" style="left:225px;top:556px" width="11" height="11"><use href="#icon-pin"/></svg>
  <div class="footer-band">421, Address line here Country Name, 45452</div>
</section>

<!-- Business card front -->
<section class="sheet card-front">
  <div class="wordmark">teva kora<span class="dot"></span></div>
  <div class="divider"></div>
  <div class="name">Daniel Morris</div>
  <div class="title">Managing Director</div>
  <ul class="contact">
    <li><svg width="6" height="6"><use href="#icon-phone"/></svg>044-987 650 412</li>
    <li><svg width="6" height="6"><use href="#icon-mail"/></svg>hello@tevakora.com</li>
    <li><svg width="6" height="6"><use href="#icon-globe"/></svg>www.tevakora.com</li>
  </ul>
  <div class="footer-rule"></div>
  <svg class="pin" style="left:96px;top:103px" width="7" height="7"><use href="#icon-pin"/></svg>
  <div class="footer-band">421, Address line goes here 45452,Country Name</div>
</section>

<!-- Business card back -->
<section class="sheet card-back">
  <div class="pattern" role="img" aria-label="Repeating brand name text pattern in muted navy tones"></div>
  <div class="wordmark light">teva kora<span class="dot"></span></div>
</section>

<!-- Envelope front -->
<section class="sheet envelope-front">
  <div class="wordmark">teva kora<span class="dot"></span></div>
  <div class="footer-rule"></div>
  <svg class="pin" style="left:226px;top:202px" width="11" height="11"><use href="#icon-pin"/></svg>
  <div class="footer-band">421, Address line here Country Name, 45452</div>
</section>

<!-- Envelope back -->
<section class="sheet envelope-back">
  <svg class="flap" width="452" height="54" viewBox="0 0 452 54" aria-hidden="true">
    <polygon points="0,0 452,0 434,54 18,54" fill="var(--navy)"/>
  </svg>
  <div class="wordmark light">teva kora<span class="dot"></span></div>
</section>

</body>
</html>
```